1 Page for Computer Repair Website

Looking for a 1 page website with a design that compliments the business card and pamphlet that have already been made (attached files). It should look business professional and easy to read. Email and phone number should be somewhere near the top of the website, visible when the page loads. I don't want any forms for people to mess with. No "Contact Us" form or entering in email for newsletter. Customers will just be looking at this site to confirm we are professionals and have our business in order.

Target Market(s)

Home and small business

Industry/Entity Type

Computer Repair

Coding

Coded - Design and coding required

Number of Pages Required

1 page

Font styles to use
Other font styles liked:
• Helvetica variations used in pamphlet and card

Colors
0455a3
cfdeed
85abd2
3276b5
85cae6
ffffff

Requirements
Must have
• Compliment the pamphlet and business card in color choices and font use. Pleasing to the eye and easy to read through categories and text.
Should not have
• Forms. No "enter name and email here" or anything of the sort.

```html
<!DOCTYPE html>
<html lang="en">
<head>
<meta charset="utf-8">
<title>Kestrel PC Care – Computer Service &amp; Repair</title>
<link href="https://fonts.googleapis.com/css2?family=Arimo:wght@400;700&display=swap" rel="stylesheet">
<style>
:root{
  --navy:#0455a3;
  --mid:#3276b5;
  --soft:#85abd2;
  --sky:#85cae6;
  --pale:#cfdeed;
  --white:#ffffff;
  --ink:#3a3f45;
  --muted:#6b7480;
  --band:#eef0f2;
  --footer:#0a3f78;
}
*{margin:0;padding:0;box-sizing:border-box}
html,body{width:696px;height:1200px;overflow:hidden}
body{font-family:Arimo,Helvetica,Arial,sans-serif;color:var(--ink);background:var(--white);position:relative}
.page{position:relative;width:696px;height:1200px}

.topbar{position:absolute;left:0;top:0;width:696px;height:70px}
.brand{position:absolute;left:40px;top:24px;display:flex;align-items:center;gap:8px}
.brand-mark{width:12px;height:12px;border-radius:50%;background:var(--mid)}
.brand-name{font-size:21px;font-weight:400;color:var(--navy);letter-spacing:.2px}
.contact{position:absolute;right:40px;top:16px;text-align:right;color:var(--navy);font-size:15px;line-height:20px}

.nav{position:absolute;left:0;top:70px;width:696px;height:34px;background:linear-gradient(var(--mid),var(--navy));display:flex;padding-left:40px}
.nav a{color:var(--white);font-size:10px;font-weight:700;text-decoration:none;line-height:34px;padding:0 18px}
.nav a.active{background:rgba(255,255,255,.15)}

.hero{position:absolute;left:0;top:104px;width:696px;height:330px;background:linear-gradient(100deg,#9aa6b3 0%,#c9d2dc 45%,#e8edf2 70%,#b7c3cf 100%)}
.hero-title{position:absolute;left:58px;top:96px;color:var(--white);font-size:27px;font-weight:400;line-height:30px;letter-spacing:.5px}
.dots{position:absolute;left:58px;top:167px;display:flex;gap:6px}
.dots span{width:7px;height:7px;border-radius:50%;background:rgba(255,255,255,.6)}
.dots span:first-child{background:var(--white)}

.features{position:absolute;left:58px;top:306px;width:580px;height:150px;display:flex}
.feature{flex:1;color:var(--white);text-align:center;padding-top:20px}
.feature:nth-child(1){background:var(--navy)}
.feature:nth-child(2){background:var(--mid)}
.feature:nth-child(3){background:var(--soft)}
.feature svg{width:30px;height:30px}
.feature h3{font-size:16px;font-weight:700;line-height:18px;margin-top:6px}
.feature p{font-size:8px;line-height:11px;margin:8px 26px 0;opacity:.9}

.welcome{position:absolute;left:58px;top:478px;width:580px;height:180px}
.welcome h2{font-size:22px;font-weight:700;color:var(--navy)}
.rule{width:300px;height:1px;background:var(--pale);margin:8px 0 10px}
.welcome p{width:300px;font-size:8px;line-height:12px;color:var(--muted);margin-bottom:8px}
.btn{display:inline-block;background:linear-gradient(var(--mid),var(--navy));color:var(--white);font-size:11px;font-weight:700;padding:8px 12px;border-radius:2px}
.video{position:absolute;left:336px;top:4px;width:240px;height:156px;background:linear-gradient(135deg,#dfe6ee,#9eb0c4 60%,#e9eef3)}
.video .play{position:absolute;left:102px;top:62px;width:36px;height:26px;border-radius:5px;background:var(--navy)}

.services{position:absolute;left:0;top:672px;width:696px;height:258px;background:var(--band)}
.services h2{position:absolute;left:58px;top:18px;font-size:22px;font-weight:700;color:var(--navy)}
.arrows{position:absolute;right:58px;top:20px;color:var(--ink);font-size:14px;font-weight:700;letter-spacing:6px}
.service-row{position:absolute;left:58px;top:54px;width:580px;display:flex;justify-content:space-between}
.service{width:180px}
.service .thumb{height:98px}
.service:nth-child(1) .thumb{background:linear-gradient(135deg,#0b1f3a,#1f4d8a 55%,#8a2530)}
.service:nth-child(2) .thumb{background:linear-gradient(135deg,#3a4250,#8a94a2 50%,#2a3140)}
.service:nth-child(3) .thumb{background:linear-gradient(135deg,#0a1424,#1d3350 55%,#0a1424)}
.service h3{font-size:12px;font-weight:700;color:var(--navy);margin:10px 0 5px}
.service p{font-size:7.5px;line-height:11px;color:var(--muted)}
.service .more{font-size:7.5px;font-weight:700;color:var(--navy);margin-top:6px}

.why{position:absolute;left:0;top:940px;width:696px;height:200px}
.why-visual{position:absolute;left:46px;top:4px;width:268px;height:186px;background:linear-gradient(120deg,#eef1f4,#c6ccd4 55%,#7f8894)}
.why-body{position:absolute;left:336px;top:26px;width:300px}
.why h2{font-size:22px;font-weight:700;color:var(--navy)}
.why ul{list-style:none;margin-bottom:12px}
.why li{font-size:8px;line-height:15px;color:var(--muted);display:flex;align-items:center;gap:6px}
.why li svg{width:8px;height:8px;flex:none}

.footer{position:absolute;left:0;top:1142px;width:696px;height:58px;background:var(--footer);color:var(--white)}
.footer-links{position:absolute;left:58px;top:16px;display:flex;gap:14px;font-size:8px;font-weight:700}
.copyright{position:absolute;left:58px;top:32px;font-size:7px;opacity:.8}
.social{position:absolute;right:58px;top:18px;display:flex;gap:6px}
.social span{width:14px;height:14px;border-radius:50%;background:var(--sky)}
.social span:nth-child(3),.social span:nth-child(5){background:#c0504d}
</style>
</head>
<body>
<div class="page">

  <header class="topbar">
    <div class="brand"><span class="brand-mark"></span><span class="brand-name">Kestrel PC Care</span></div>
    <div class="contact">Call us: 612-555-0148<br>Email: sam@kestrelpc.com</div>
  </header>

  <nav class="nav">
    <a class="active">HOME</a><a>ABOUT US</a><a>SERVICES</a><a>WHY CHOOSE US</a><a>CONTACT</a>
  </nav>

  <section class="hero" role="img" aria-label="Hands typing on a laptop keyboard">
    <h1 class="hero-title">COMPUTER<br>SERVICE &amp; REPAIR</h1>
    <div class="dots"><span></span><span></span><span></span></div>
  </section>

  <section class="features">
    <div class="feature">
      <svg viewBox="0 0 30 30"><path d="M3 15 15 4l12 11h-4v11h-6v-7h-4v7H7V15z" fill="#fff"/></svg>
      <h3>RESIDENTIAL<br>SERVICES</h3>
      <p>Friendly help at home for laptops, desktops, printers and wireless networks.</p>
    </div>
    <div class="feature">
      <svg viewBox="0 0 30 30"><path d="M6 26V4h18v22zM9 7h4v3H9zm8 0h4v3h-4zM9 13h4v3H9zm8 0h4v3h-4zM9 19h4v3H9zm8 0h4v3h-4z" fill="#fff" fill-rule="evenodd"/></svg>
      <h3>BUSINESS<br>SERVICES</h3>
      <p>Reliable support for office computers, servers and shared networks.</p>
    </div>
    <div class="feature">
      <svg viewBox="0 0 30 30"><rect x="3" y="5" width="24" height="16" fill="none" stroke="#fff" stroke-width="2"/><path d="M11 25h8M15 21v4" stroke="#fff" stroke-width="2"/></svg>
      <h3>REMOTE<br>SUPPORT</h3>
      <p>Secure remote sessions that fix common problems without a visit.</p>
    </div>
  </section>

  <section class="welcome">
    <h2>WELCOME TO KESTREL</h2>
    <div class="rule"></div>
    <p>We repair, upgrade and maintain computers for homes and small offices across the city. Every job is handled by certified technicians with clear pricing.</p>
    <p>From slow laptops to failed drives, we diagnose the problem quickly and explain your options in plain language before any work begins.</p>
    <span class="btn">Request Quote</span>
    <div class="video" role="img" aria-label="Video preview showing desktop computer monitors"><span class="play"></span></div>
  </section>

  <section class="services">
    <h2>OUR SERVICES</h2>
    <div class="arrows">‹ ›</div>
    <div class="service-row">
      <article class="service">
        <div class="thumb" role="img" aria-label="Circuit board with a warning glow"></div>
        <h3>MALWARE/VIRUS REMOVAL</h3>
        <p>Infections are cleaned out thoroughly and your system is protected against future threats and unwanted pop-ups.</p>
        <div class="more">Read More</div>
      </article>
      <article class="service">
        <div class="thumb" role="img" aria-label="Close view of computer hardware components"></div>
        <h3>HARDWARE REPAIR</h3>
        <p>Faulty screens, drives, memory and power parts are replaced with quality components and tested carefully.</p>
        <div class="more">Read More</div>
      </article>
      <article class="service">
        <div class="thumb" role="img" aria-label="Padlock over a digital data background"></div>
        <h3>DATA MIGRATION</h3>
        <p>Files, photos and settings are moved safely to your new machine with nothing left behind.</p>
        <div class="more">Read More</div>
      </article>
    </div>
  </section>

  <section class="why">
    <div class="why-visual" role="img" aria-label="Laptop with a hand reaching out of the screen"></div>
    <div class="why-body">
      <h2>WHY CHOOSE US</h2>
      <div class="rule"></div>
      <ul>
        <li><svg viewBox="0 0 8 8"><path d="M1 4l2 2 4-5" fill="none" stroke="#3276b5" stroke-width="1.5"/></svg>Certified technicians with years of hands-on experience</li>
        <li><svg viewBox="0 0 8 8"><path d="M1 4l2 2 4-5" fill="none" stroke="#3276b5" stroke-width="1.5"/></svg>Fair, upfront pricing with no hidden fees</li>
        <li><svg viewBox="0 0 8 8"><path d="M1 4l2 2 4-5" fill="none" stroke="#3276b5" stroke-width="1.5"/></svg>Fast turnaround on most repairs and upgrades</li>
        <li><svg viewBox="0 0 8 8"><path d="M1 4l2 2 4-5" fill="none" stroke="#3276b5" stroke-width="1.5"/></svg>Secure handling of your files and privacy</li>
        <li><svg viewBox="0 0 8 8"><path d="M1 4l2 2 4-5" fill="none" stroke="#3276b5" stroke-width="1.5"/></svg>Service for both home and small business</li>
      </ul>
      <span class="btn">Request Quote</span>
    </div>
  </section>

  <footer class="footer">
    <div class="footer-links"><span>HOME</span><span>ABOUT US</span><span>SERVICES</span><span>WHY CHOOSE US</span><span>CONTACT</span></div>
    <div class="copyright">© 2024 Kestrel PC Care. All rights reserved.</div>
    <div class="social"><span></span><span></span><span></span><span></span><span></span></div>
  </footer>

</div>
</body>
</html>
```